Ductless Mini Split Business Website

Copper Fern Services is looking to design an eye catching educational website about installing Ductless mini splits.

Similar to this company.
https://www.halvikstream.com/

Coding

Coded - Design and coding required

```html
<!DOCTYPE html>
<html lang="en">
<head>
<meta charset="utf-8">
<title>Copper Fern Services – Website Layouts</title>
<link href="https://fonts.googleapis.com/css2?family=Montserrat:wght@400;600;700;800&display=swap" rel="stylesheet">
<style>
:root{
  --ink:#1e232c;
  --ink-2:#2a303b;
  --yellow:#f5c518;
  --yellow-deep:#e2ad00;
  --paper:#ffffff;
  --mist:#f3f3f3;
  --text:#4a4f58;
  --soft:#9aa0aa;
  --photo-a:#c9d3de;
  --photo-b:#8e9aa8;
}
*{box-sizing:border-box;margin:0;padding:0}
html,body{width:779px;height:1200px;overflow:hidden;background:var(--paper);font-family:"Montserrat",Arial,sans-serif;color:var(--text)}
.canvas{position:relative;width:779px;height:1200px;background:#fafafa}
.page{position:absolute;top:40px;width:346px;background:var(--paper);box-shadow:0 1px 6px rgba(0,0,0,.18);overflow:hidden}
.page--classic{left:44px;height:1104px}
.page--angled{left:400px;height:1136px}
.band{position:absolute;left:0;width:100%}
.dark{background:var(--ink);color:#fff}

/* header */
.topbar{top:0;height:34px;display:flex;align-items:center;justify-content:space-between;padding:0 14px;background:var(--paper)}
.topbar__contact{display:flex;align-items:center;gap:4px;font-size:4.5px;color:var(--ink)}
.dot{width:9px;height:9px;border-radius:50%;background:var(--ink);display:inline-block}
.brand{font-weight:800;font-size:9px;color:var(--yellow-deep);display:flex;align-items:center;gap:4px}
.brand__mark{width:10px;height:10px;border-radius:50%;background:var(--yellow)}
.btn{display:inline-block;background:var(--yellow);color:var(--ink);font-weight:700;font-size:5px;padding:3px 8px;border-radius:8px}
.nav{top:34px;height:16px;background:var(--ink);display:flex;align-items:center;justify-content:center;gap:14px;font-size:4.5px;color:#fff}
.nav span:first-child{color:var(--yellow)}

/* hero */
.hero{top:50px;background:linear-gradient(110deg,#e9edf1 0%,var(--photo-a) 45%,var(--photo-b) 100%)}
.hero__text{position:absolute;left:18px;top:46px;width:150px}
.hero h1{font-size:19px;font-weight:800;color:var(--yellow);line-height:1.1;margin-bottom:6px}
.hero p{font-size:4.5px;line-height:1.5;color:var(--ink);margin-bottom:8px}

/* generic section type */
.title{font-size:11px;font-weight:700;color:var(--ink);text-align:center}
.title em{font-style:normal;color:var(--yellow-deep)}
.dark .title{color:#fff}
.dark .title em{color:var(--yellow)}
.copy{font-size:4.3px;line-height:1.6;text-align:center;color:var(--text)}
.dark .copy{color:#c9ccd2}

/* welcome */
.welcome .title{margin-top:26px}
.welcome .copy{width:250px;margin:10px auto 10px}
.welcome__actions{display:flex;justify-content:center;gap:8px}
.btn--dark{background:var(--ink);color:#fff}

/* why */
.why__head{position:absolute;left:20px;top:34px}
.why__head h2{font-size:11px;font-weight:600;color:#fff;line-height:1.2}
.why__head h2 em{font-style:normal;color:var(--yellow);font-weight:700}
.why__mascot{position:absolute;left:70px;top:72px;width:66px;height:58px;border-radius:50%;background:radial-gradient(circle,var(--yellow) 0%,#b78b00 70%,transparent 71%)}
.why__list{position:absolute;left:180px;top:30px;width:150px;display:flex;flex-direction:column;gap:10px}
.why__item{display:flex;gap:5px;font-size:4.3px;line-height:1.5;color:#c9ccd2}
.why__item b{display:block;color:#fff;font-size:5px}
.why__icon{flex:0 0 10px;height:10px;border-radius:50%;background:var(--yellow)}

/* stand behind */
.stand .title{margin-top:22px}
.stand__grid{position:absolute;left:16px;right:16px;top:52px;display:flex;gap:6px}
.card{flex:1;text-align:center}
.card__photo{height:46px;background:linear-gradient(135deg,#eef1f4,var(--photo-a) 60%,var(--photo-b))}
.card p{font-size:4.3px;font-weight:600;color:var(--ink);margin-top:4px;line-height:1.4}

/* contact */
.contact__person{position:absolute;left:18px;bottom:0;width:90px;top:14px;background:linear-gradient(180deg,#3a4452,#222831)}
.contact__form{position:absolute;left:130px;top:18px;width:196px}
.contact__form .title{text-align:left;margin-bottom:10px}
.field-row{display:flex;gap:6px;margin-bottom:6px}
.field{flex:1;height:12px;background:#fff;border-radius:1px;font-size:4px;color:var(--soft);padding:4px 4px}
.field--area{height:24px}

/* testimonials */
.testimonials .title{margin-top:22px}
.quote-card{position:absolute;left:32px;right:32px;top:50px}
.avatar{position:absolute;left:0;top:0;width:46px;height:46px;border-radius:50%;background:radial-gradient(circle,#7a5a44,#3f2d22)}
.quote-card__body{margin-left:60px;font-size:4.3px;line-height:1.6}
.quote-card__body b{display:block;color:var(--yellow-deep);font-size:5px;margin-top:4px}
.quote-mark{position:absolute;font-size:26px;font-weight:800;color:var(--yellow);line-height:1}
.pager{position:absolute;bottom:16px;left:0;right:0;display:flex;justify-content:center;gap:3px}
.pager i{width:4px;height:4px;border-radius:50%;background:#ccc}
.pager i:first-child{background:var(--yellow)}

/* footer */
.newsletter{position:absolute;left:18px;right:18px;height:40px;background:var(--yellow);display:flex;align-items:center;justify-content:space-between;padding:0 14px}
.newsletter h3{font-size:9px;font-weight:700;color:var(--ink)}
.newsletter__input{width:74px;height:12px;background:#fff;border-radius:6px;font-size:4px;color:var(--soft);padding:4px 6px}
.footer__brand{position:absolute;left:0;right:0;display:flex;justify-content:center}
.footer__links{position:absolute;left:0;right:0;display:flex;justify-content:center;gap:12px;font-size:4.5px;color:#fff}
.footer__copy{position:absolute;left:0;right:0;text-align:center;font-size:4px;color:var(--soft)}
.footer__rule{position:absolute;left:18px;right:18px;height:1px;background:#3a404b}
</style>
</head>
<body>
<div class="canvas">

  <!-- ===== Classic layout ===== -->
  <section class="page page--classic">
    <header class="band topbar">
      <div class="topbar__contact"><span class="dot"></span>Call Us Today<br>(555) 014-2290</div>
      <div class="brand"><span class="brand__mark"></span>Copper Fern Services</div>
      <span class="btn">Get a Quote</span>
    </header>
    <nav class="band nav"><span>Home</span><span>About Us</span><span>Ductless Mini Splits</span><span>Services</span><span>Gallery</span><span>Contact</span></nav>

    <div class="band hero" style="height:153px" role="img" aria-label="Technician installing a wall-mounted ductless mini split unit">
      <div class="hero__text">
        <h1>Copper Fern Services</h1>
        <p>Quiet, efficient comfort for every room. We install and service ductless systems across the valley.</p>
        <span class="btn">Learn More</span>
      </div>
    </div>

    <div class="band welcome" style="top:203px;height:103px">
      <h2 class="title">Welcome To <em>Copper Fern Services</em></h2>
      <p class="copy">Ductless mini splits bring heating and cooling to any space without bulky ductwork. Our certified team guides you from sizing and placement to clean installation, so your home stays comfortable all year while energy bills stay low.</p>
      <div class="welcome__actions"><span class="btn">About Us</span><span class="btn btn--dark">Our Services</span></div>
    </div>

    <div class="band why dark" style="top:306px;height:144px">
      <div class="why__head"><h2>Why Choose<br><em>Copper Fern Services</em></h2></div>
      <div class="why__mascot" role="img" aria-label="Cartoon mascot illustration"></div>
      <div class="why__list">
        <div class="why__item"><span class="why__icon"></span><div><b>We Are Licensed &amp; Insured</b>Trained pros with years of field work.</div></div>
        <div class="why__item"><span class="why__icon"></span><div><b>Fast, Friendly Service</b>Same week visits and clear pricing.</div></div>
        <div class="why__item"><span class="why__icon"></span><div><b>Mini Split Experts</b>We focus on ductless systems only.</div></div>
      </div>
    </div>

    <div class="band stand" style="top:450px;height:130px">
      <h2 class="title">We Stand Behind <em>Our Excellent Services</em></h2>
      <div class="stand__grid">
        <div class="card"><div class="card__photo" role="img" aria-label="Indoor wall unit"></div><p>Installation</p></div>
        <div class="card"><div class="card__photo" role="img" aria-label="Technician servicing unit"></div><p>Repair</p></div>
        <div class="card"><div class="card__photo" role="img" aria-label="Outdoor condenser"></div><p>Maintenance</p></div>
        <div class="card"><div class="card__photo" role="img" aria-label="Remote control and unit"></div><p>Consultation</p></div>
      </div>
    </div>

    <div class="band contact dark" style="top:580px;height:156px">
      <div class="contact__person" role="img" aria-label="Technician standing with arms crossed"></div>
      <div class="contact__form">
        <h2 class="title">Contact Us Today</h2>
        <div class="field-row"><div class="field">Name</div><div class="field">Email</div></div>
        <div class="field-row"><div class="field">Phone</div><div class="field">Service</div></div>
        <div class="field-row"><div class="field field--area">Message</div></div>
        <span class="btn">Submit</span>
      </div>
    </div>

    <div class="band testimonials" style="top:736px;height:156px">
      <h2 class="title">Testimonials</h2>
      <div class="quote-card">
        <div class="avatar" role="img" aria-label="Customer portrait"></div>
        <span class="quote-mark" style="left:46px;top:-8px">&ldquo;</span>
        <div class="quote-card__body">The crew was on time, tidy and explained every step. Our upstairs is finally cool in summer and the unit is so quiet we forget it is running. Highly recommend this team.<b>Dana Whitlock</b></div>
        <span class="quote-mark" style="right:-6px;top:42px">&rdquo;</span>
      </div>
      <div class="pager"><i></i><i></i><i></i></div>
    </div>

    <footer class="band dark" style="top:892px;height:212px">
      <div class="newsletter" style="top:8px"><h3>Subscribe to our Newsletter</h3><div class="newsletter__input">Enter email</div></div>
      <div class="footer__brand" style="top:86px"><span class="brand"><span class="brand__mark"></span>Copper Fern Services</span></div>
      <div class="footer__links" style="top:122px"><span>Home</span><span>About Us</span><span>Services</span><span>Gallery</span><span>Contact</span></div>
      <div class="footer__rule" style="top:150px"></div>
      <div class="footer__copy" style="top:168px">© 2024 Copper Fern Services. All rights reserved.</div>
    </footer>
  </section>

  <!-- ===== Angled layout ===== -->
  <section class="page page--angled">
    <header class="band topbar">
      <div class="topbar__contact"><span class="dot"></span>Call Us Today<br>(555) 014-2290</div>
      <div class="brand"><span class="brand__mark"></span>Copper Fern Services</div>
      <span class="btn">Get a Quote</span>
    </header>
    <nav class="band nav"><span>Home</span><span>About Us</span><span>Ductless Mini Splits</span><span>Services</span><span>Gallery</span><span>Contact</span></nav>

    <div class="band hero" style="height:170px;clip-path:polygon(0 0,100% 0,100% 82%,0 100%)" role="img" aria-label="Technician installing a ductless unit on a brick wall">
      <div class="hero__text" style="top:50px">
        <h1>Copper Fern Services</h1>
        <p>Quiet, efficient comfort for every room. We install and service ductless systems across the valley.</p>
        <span class="btn">Learn More</span>
      </div>
    </div>

    <div class="band welcome" style="top:226px;height:120px">
      <h2 class="title">Welcome To <em>Copper Fern Services</em></h2>
      <p class="copy">Ductless mini splits bring heating and cooling to any space without bulky ductwork. Our certified team guides you from sizing and placement to clean installation, so your home stays comfortable all year while energy bills stay low.</p>
      <div class="welcome__actions"><span class="btn">About Us</span><span class="btn btn--dark">Our Services</span></div>
    </div>

    <svg class="band" style="top:330px;height:200px" width="346" height="200" viewBox="0 0 346 200" aria-hidden="true">
      <polygon points="0,22 346,0 346,170 0,200" fill="#1e232c"/>
      <polygon points="0,185 346,150 346,176 0,200" fill="#f5c518"/>
    </svg>
    <div class="band why" style="top:340px;height:170px">
      <div class="why__head"><h2>Why Choose<br><em>Copper Fern Services</em></h2></div>
      <div class="why__mascot" style="top:78px" role="img" aria-label="Cartoon mascot illustration"></div>
      <div class="why__list" style="top:32px">
        <div class="why__item"><span class="why__icon"></span><div><b>We Are Licensed &amp; Insured</b>Trained pros with years of field work.</div></div>
        <div class="why__item"><span class="why__icon"></span><div><b>Fast, Friendly Service</b>Same week visits and clear pricing.</div></div>
        <div class="why__item"><span class="why__icon"></span><div><b>Mini Split Experts</b>We focus on ductless systems only.</div></div>
      </div>
    </div>

    <div class="band stand" style="top:540px;height:140px">
      <h2 class="title" style="margin-top:10px">We Stand Behind <em>Our Excellent Services</em></h2>
      <div class="stand__grid" style="top:40px">
        <div class="card"><div class="card__photo" style="height:52px" role="img" aria-label="Indoor wall unit"></div><p>Installation</p></div>
        <div class="card"><div class="card__photo" style="height:52px" role="img" aria-label="Technician servicing unit"></div><p>Repair</p></div>
        <div class="card"><div class="card__photo" style="height:52px" role="img" aria-label="Outdoor condenser"></div><p>Maintenance</p></div>
        <div class="card"><div class="card__photo" style="height:52px" role="img" aria-label="Remote control and unit"></div><p>Consultation</p></div>
      </div>
    </div>

    <div class="band contact dark" style="top:670px;height:190px;clip-path:polygon(0 12%,100% 0,100% 88%,0 100%)">
      <div class="contact__person" style="top:30px;bottom:10px" role="img" aria-label="Technician standing with arms crossed"></div>
      <div class="contact__form" style="top:34px">
        <h2 class="title">Contact Us Today</h2>
        <div class="field-row"><div class="field">Name</div><div class="field">Email</div></div>
        <div class="field-row"><div class="field">Phone</div><div class="field">Service</div></div>
        <div class="field-row"><div class="field field--area">Message</div></div>
        <span class="btn">Submit</span>
      </div>
    </div>

    <div class="band testimonials" style="top:860px;height:140px">
      <h2 class="title" style="margin-top:14px">Testimonials</h2>
      <div class="quote-card" style="top:40px">
        <div class="avatar" role="img" aria-label="Customer portrait"></div>
        <span class="quote-mark" style="left:46px;top:-8px">&ldquo;</span>
        <div class="quote-card__body">The crew was on time, tidy and explained every step. Our upstairs is finally cool in summer and the unit is so quiet we forget it is running. Highly recommend this team.<b>Dana Whitlock</b></div>
        <span class="quote-mark" style="right:-6px;top:42px">&rdquo;</span>
      </div>
      <div class="pager" style="bottom:8px"><i></i><i></i><i></i></div>
    </div>

    <footer class="band dark" style="top:1000px;height:136px;clip-path:polygon(0 14%,100% 0,100% 100%,0 100%)">
      <div class="newsletter" style="top:20px;left:10px;right:30px"><h3>Subscribe to our Newsletter</h3><div class="newsletter__input">Enter email</div></div>
      <div class="footer__brand" style="top:74px"><span class="brand"><span class="brand__mark"></span>Copper Fern Services</span></div>
      <div class="footer__links" style="top:96px"><span>Home</span><span>About Us</span><span>Services</span><span>Gallery</span><span>Contact</span></div>
      <div class="footer__copy" style="top:118px">© 2024 Copper Fern Services. All rights reserved.</div>
    </footer>
  </section>

</div>
</body>
</html>
```